Looking for a modern, Professional business card design

We have a simple business card, but are looking for a more modern, professional look. A sample of the basic card is attached as well as the logo. We would also like to add that we offer:
Struggling with your finances?
- Learn to become debt free
- Discover the power of cash
- Control your money instead of it controlling you
Let us help you achieve a new level of financial freedom!
Also, we would like to have a "SPECIAL OFFER!: FREE 30 minute consultation"
Financial Planning

```html
<!DOCTYPE html>
<html lang="en">
<head>
<meta charset="utf-8">
<title>Clearpath Financial Coaching – Business Card</title>
<link rel="stylesheet" href="https://fonts.googleapis.com/css2?family=Arimo:wght@400;700&display=swap">
<style>
  :root {
    --page-bg: #e9ebe8;
    --green-dark: #2f8a1f;
    --green-mid: #4fae2c;
    --green-light: #8fd04a;
    --green-text: #5cae2c;
    --ink: #222222;
    --ink-soft: #444444;
    --white: #ffffff;
    --card-shadow: 0 10px 30px rgba(0,0,0,0.18);
  }
  * { box-sizing: border-box; margin: 0; padding: 0; }
  html, body {
    width: 1200px; height: 950px; overflow: hidden;
    background: var(--page-bg);
    font-family: "Arimo", Arial, sans-serif;
  }
  .sheet {
    position: relative; width: 1200px; height: 950px;
    display: flex; flex-direction: column; align-items: center; justify-content: center; gap: 50px;
  }
  .card {
    position: relative; width: 700px; height: 400px;
    box-shadow: var(--card-shadow); overflow: hidden;
  }

  /* Back side */
  .card--back {
    background: radial-gradient(ellipse at 50% 40%, var(--green-light) 0%, var(--green-mid) 45%, var(--green-dark) 100%);
    color: var(--white);
    text-align: center;
    padding-top: 60px;
  }
  .brand {
    display: inline-flex; align-items: center; gap: 14px;
  }
  .brand__dot {
    width: 34px; height: 34px; border-radius: 50%;
  }
  .brand__name {
    font-weight: 700; font-size: 30px; letter-spacing: 0.5px;
  }
  .card--back .brand__dot { background: var(--white); }
  .card--back .brand__name { color: var(--white); }
  .tagline {
    font-size: 13px; margin-top: 8px; opacity: 0.9;
  }
  .offer-list { margin-top: 44px; }
  .offer-list__heading {
    font-weight: 700; font-size: 19px; letter-spacing: 0.5px; margin-bottom: 10px;
  }
  .offer-list__line {
    font-size: 16px; line-height: 1.5;
  }
  .special-offer {
    margin-top: 26px; font-weight: 700; font-size: 19px;
  }

  /* Front side */
  .card--front { background: var(--white); }
  .card__watermark {
    position: absolute; left: -80px; top: 60px;
    width: 340px; height: 340px; border-radius: 50%;
    background: var(--green-light); opacity: 0.12;
  }
  .person {
    position: absolute; left: 48px; top: 44px;
  }
  .person__name { color: var(--green-text); font-size: 24px; }
  .person__role { color: var(--ink); font-size: 18px; margin-top: 6px; }
  .contact {
    position: absolute; left: 48px; bottom: 48px;
    color: var(--ink-soft); font-size: 18px; line-height: 1.45;
  }
  .contact__label { color: var(--green-text); font-weight: 700; }
  .card--front .brand {
    position: absolute; right: 44px; top: 180px;
  }
  .card--front .brand__dot { background: var(--green-mid); }
  .card--front .brand__name { color: var(--ink); font-size: 26px; }
  .card--front .tagline {
    position: absolute; right: 44px; top: 226px; color: var(--ink-soft); opacity: 1;
  }
</style>
</head>
<body>
<main class="sheet">
  <section class="card card--back" aria-label="Card back">
    <div class="brand">
      <span class="brand__dot"></span>
      <span class="brand__name">Clearpath Financial Coaching</span>
    </div>
    <p class="tagline">Achieve a new level of personal freedom</p>
    <div class="offer-list">
      <p class="offer-list__heading">STRUGGLING WITH YOUR FINANCES?</p>
      <p class="offer-list__line">Learn to become debt free &bull; Discover the power of cash</p>
      <p class="offer-list__line">Control your money instead of it controlling you</p>
      <p class="offer-list__line">Let us help you achieve a new level of financial freedom!</p>
    </div>
    <p class="special-offer">SPECIAL OFFER: FREE 30 minute consultation</p>
  </section>

  <section class="card card--front" aria-label="Card front">
    <span class="card__watermark"></span>
    <div class="person">
      <p class="person__name">Daniel R. Whitfield</p>
      <p class="person__role">Personal Financial Coach</p>
    </div>
    <div class="brand">
      <span class="brand__dot"></span>
      <span class="brand__name">Clearpath Financial Coaching</span>
    </div>
    <p class="tagline">Achieve a new level of personal freedom</p>
    <div class="contact">
      <p><span class="contact__label">Mob:</span> (205) 555-0187</p>
      <p>daniel@clearpathcoaching.com</p>
      <p>www.clearpathcoaching.com</p>
    </div>
  </section>
</main>
</body>
</html>
```